Thornvale Group needs a business card design

We need a new business card design using the logo recently selected in a logo competition on Pixel Bazaar. Our business is a consultancy specializing in aviation and energy and the winning business card design will promote an image of precision and professionalism with creativity.

Please use the logo with the name on the front of the card and use a complementary font. Make the back white with either the light grey or dark grey logo.

Target Market(s)

Senior finance and legal leaders at aviation and energy companies

Industry/Entity Type

Management Consulting

Contact Information for Business Card

Peter Castrell
President
Thornvale Group

www.thornvalegroup.example

(555) 204-6391
pc@thornvalegroup.example

Requirements
Must have
• Professional font that goes well with the logo font

```html
<!DOCTYPE html>
<html lang="en">
<head>
<meta charset="utf-8">
<title>Thornvale Group – Business Card</title>
<link href="https://fonts.googleapis.com/css2?family=Open+Sans:wght@400;600;700&display=swap" rel="stylesheet">
<style>
  :root {
    --navy: #0f3f6e;
    --slate: #646567;
    --paper: #ffffff;
    --backdrop: #e9e9ea;
    --muted: #5a5b5d;
  }
  * { margin: 0; padding: 0; box-sizing: border-box; }
  html, body {
    width: 1200px; height: 900px; overflow: hidden;
    background: var(--backdrop);
    font-family: "Open Sans", Arial, sans-serif;
  }
  .canvas { position: relative; width: 1200px; height: 900px; }
  .card {
    position: absolute;
    background: var(--paper);
    box-shadow: 0 6px 18px rgba(0,0,0,0.18);
    overflow: hidden;
  }
  .card-front { left: 238px; top: 60px; width: 556px; height: 345px; }
  .card-back  { left: 457px; top: 518px; width: 560px; height: 343px; }

  .front-bands { position: absolute; inset: 0; }
  .band-slate { fill: var(--slate); }
  .band-navy { fill: var(--navy); }

  .front-wordmark {
    position: absolute; left: 22px; top: 108px;
    color: var(--navy); font-weight: 400; font-size: 27px;
    letter-spacing: 1px;
  }

  .contact {
    position: absolute; right: 42px; top: 203px;
    text-align: right; color: var(--paper);
  }
  .contact-name { font-weight: 700; font-size: 17px; line-height: 22px; margin-right: -1px; }
  .contact-title { font-size: 14px; line-height: 18px; margin-bottom: 19px; margin-right: -1px; }
  .contact-line {
    font-size: 14px; line-height: 20px;
    display: flex; justify-content: flex-end; align-items: center; gap: 8px;
    margin-right: -20px;
  }
  .contact-line svg { width: 12px; height: 12px; fill: var(--paper); }

  .back-wordmark {
    position: absolute; left: 0; right: 0; top: 92px;
    text-align: center; color: var(--navy);
    font-weight: 400; font-size: 44px; letter-spacing: 2px;
  }
  .back-service {
    position: absolute; left: 0; right: 0; top: 243px;
    text-align: center; color: var(--navy);
    font-weight: 700; font-size: 16px; letter-spacing: -0.2px;
  }
  .back-sectors {
    position: absolute; left: 0; right: 0; top: 270px;
    text-align: center; color: var(--muted);
    font-size: 16px; letter-spacing: -0.2px;
  }
</style>
</head>
<body>
<main class="canvas">
  <section class="card card-front" aria-label="Business card front">
    <svg class="front-bands" viewBox="0 0 556 345" width="556" height="345" aria-hidden="true">
      <polygon class="band-slate" points="425,0 437,0 198,345 0,345 0,332"/>
      <polygon class="band-navy" points="443,0 556,0 556,345 203,345"/>
    </svg>
    <div class="front-wordmark">Thornvale Group</div>
    <div class="contact">
      <div class="contact-name">Peter Castrell</div>
      <div class="contact-title">President</div>
      <div class="contact-line">(555) 204-6391
        <svg viewBox="0 0 24 24" aria-hidden="true"><path d="M6.6 10.8a15.2 15.2 0 0 0 6.6 6.6l2.2-2.2a1 1 0 0 1 1-.25 11.4 11.4 0 0 0 3.6.57 1 1 0 0 1 1 1V20a1 1 0 0 1-1 1A17 17 0 0 1 3 4a1 1 0 0 1 1-1h3.5a1 1 0 0 1 1 1c0 1.25.2 2.45.57 3.57a1 1 0 0 1-.25 1z"/></svg>
      </div>
      <div class="contact-line">pc@thornvalegroup.example
        <svg viewBox="0 0 24 24" aria-hidden="true"><path d="M2 5h20v14H2z M3.5 6.5 12 13l8.5-6.5" stroke="#0f3f6e" stroke-width="1.6"/></svg>
      </div>
    </div>
  </section>

  <section class="card card-back" aria-label="Business card back">
    <div class="back-wordmark">Thornvale Group</div>
    <div class="back-service">Finance and Strategy Consulting</div>
    <div class="back-sectors">Aviation - Manufacturing - Energy</div>
  </section>
</main>
</body>
</html>
```